KDWB Business Card

Looking for a business card design to incorporate our branding. We want to only use the colors listing in the Branding Package (attached).
Updates

Target Market(s)

People who need their phone or device fixed.

Industry/Entity Type

Electronics

Contact Information for Business Card

Please use:

Brightwick Gadget Clinic LLC
4810 E Harlow Ridge Rd
Suite 417
San Antonio, TX 78163

Marcus Delgrove, Store Manager

(210) 555-0147

Requirements
Must have
• Must include the colors that are contained within the Branding Package PDF file.

```html
<!DOCTYPE html>
<html lang="en">
<head>
<meta charset="utf-8">
<title>Brightwick Gadget Clinic – Business Card</title>
<link rel="stylesheet" href="https://fonts.googleapis.com/css2?family=Comfortaa:wght@400&family=Arimo:wght@400&display=swap">
<style>
  :root {
    --bg: #3a312c;
    --card: #1c1c1c;
    --card-edge: #262626;
    --brand-orange: #ee5a24;
    --text-light: #f2f2f2;
    --text-muted: #8a8a8a;
    --divider: #4a4a4a;
  }
  * { margin: 0; padding: 0; box-sizing: border-box; }
  html, body { width: 1200px; height: 810px; overflow: hidden; }
  body {
    background: var(--bg);
    font-family: "Arimo", Arial, sans-serif;
    position: relative;
  }
  .card {
    position: absolute;
    width: 540px;
    height: 309px;
    background: linear-gradient(135deg, var(--card-edge), var(--card));
    border-radius: 18px;
    box-shadow: 0 14px 30px rgba(0,0,0,0.45);
    overflow: hidden;
  }
  .card--front { left: 40px; top: 110px; }
  .card--back { left: 620px; top: 390px; }

  .brand {
    position: absolute;
    display: flex;
    align-items: center;
    gap: 12px;
  }
  .brand__mark {
    width: 34px;
    height: 34px;
    border-radius: 8px;
    background: var(--brand-orange);
    flex: none;
  }
  .brand__name {
    font-family: "Comfortaa", sans-serif;
    font-weight: 400;
    color: var(--brand-orange);
    font-size: 22px;
    white-space: nowrap;
  }
  .card--front .brand { left: 50%; top: 50%; transform: translate(-50%, -50%); }

  .card--back .brand { left: 30px; top: 134px; }
  .card--back .brand__mark { width: 28px; height: 28px; border-radius: 7px; }
  .card--back .brand__name { font-size: 17px; }

  .divider {
    position: absolute;
    left: 306px;
    top: 40px;
    width: 1px;
    height: 229px;
    background: linear-gradient(to bottom, transparent, var(--divider), transparent);
  }

  .contact {
    position: absolute;
    left: 330px;
    top: 78px;
    color: var(--text-light);
  }
  .contact__name { font-size: 21px; letter-spacing: 0.3px; }
  .contact__role { font-size: 12px; color: var(--brand-orange); margin-top: 2px; }
  .contact__phone { font-size: 14px; margin-top: 26px; }
  .contact__line { font-size: 13px; margin-top: 12px; }
  .contact__line + .contact__line { margin-top: 6px; }
</style>
</head>
<body>
  <section class="card card--front" aria-label="Card front">
    <div class="brand">
      <span class="brand__mark"></span>
      <span class="brand__name">Brightwick Gadget Clinic</span>
    </div>
  </section>

  <section class="card card--back" aria-label="Card back">
    <div class="brand">
      <span class="brand__mark"></span>
      <span class="brand__name">Brightwick Gadget Clinic</span>
    </div>
    <div class="divider"></div>
    <div class="contact">
      <p class="contact__name">Marcus Delgrove</p>
      <p class="contact__role">Store Manager</p>
      <p class="contact__phone">(210) 555-0147</p>
      <p class="contact__line">marcus@brightwickclinic.com</p>
      <p class="contact__line">www.brightwickclinic.com</p>
    </div>
  </section>
</body>
</html>
```